Design a Cover for a Book on Innovation

I need a design for my book: The Quiet Harvest of Invention
It is about the following:

Innovation is not just for those endowed with special talent or skills in technology. This book describes the thought framework that consists of seven principal differences between the current period and the past. Innovation is happening along these shifts. Understanding the differences can allow for consistent innovation and the identification of real opportunities.
Updates

To All: All of you show great talent as designers. I've added a bit more to the description. Feel free to ask questions. Best, DT

Font styles to use
Sans Serif

Colors

Designer to choose colors to be used in the design.

Requirements
Must have
• It should feel modern and innovative. It should incorporate the meaning of Quiet Harvest.
Nice to have
• It should have the title, and a holder spot for the subtitle and author's name Dara Tovens
Should not have
• It should not be overly busy. Sleek modern design that still gets the point across. Alternatively an image that is a full cover graphic.

```html
<!DOCTYPE html>
<html lang="en">
<head>
<meta charset="utf-8">
<title>The Quiet Harvest of Invention — Cover Spread</title>
<link rel="stylesheet" href="https://fonts.googleapis.com/css2?family=Raleway:ital,wght@0,300;0,400;0,700;1,300&display=swap">
<style>
  :root {
    --backdrop: #bfbeba;
    --cover-yellow: #e0bf00;
    --front-yellow: #e6c700;
    --front-glow: #ecd23a;
    --spine-yellow: #dcbc00;
    --ink: #35332a;
    --subtitle-ink: #a8800a;
  }
  * { margin: 0; padding: 0; box-sizing: border-box; }
  html, body {
    width: 1200px; height: 1200px; overflow: hidden;
    background: var(--backdrop);
    font-family: "Raleway", sans-serif;
    color: var(--ink);
  }
  .spread {
    position: absolute; left: 50px; top: 258px;
    width: 1100px; height: 683px;
    background: var(--cover-yellow);
    box-shadow: 0 2px 6px rgba(0,0,0,0.18);
  }
  .back-cover { position: absolute; left: 0; top: 0; width: 525px; height: 683px; }
  .spine {
    position: absolute; left: 525px; top: 0; width: 50px; height: 683px;
    background: var(--spine-yellow);
  }
  .front-cover {
    position: absolute; left: 575px; top: 0; width: 525px; height: 683px;
  }
  .front-photo {
    position: absolute; inset: 0;
    background: radial-gradient(ellipse at 55% 35%, var(--front-glow) 0%, var(--front-yellow) 60%);
  }

  .stacked-title {
    position: absolute; text-align: right;
    font-weight: 300; font-size: 27px; line-height: 26px; letter-spacing: -0.3px;
  }
  .back-cover .stacked-title { right: 97px; top: 95px; }
  .title-rule {
    position: absolute; left: 0; top: 245px; width: 290px;
    border-top: 1px solid var(--ink);
  }
  .subtitle {
    position: absolute; left: 0; width: 100%; text-align: center;
    font-style: italic; font-weight: 300; font-size: 12.5px;
    text-transform: uppercase; color: var(--subtitle-ink); letter-spacing: 0.2px;
  }
  .author {
    position: absolute; left: 0; width: 100%; text-align: center;
    font-weight: 700; font-size: 11px; letter-spacing: 0.4px; text-transform: uppercase;
  }
  .back-cover .subtitle { top: 286px; }
  .back-cover .author { top: 322px; }
  .blurb {
    position: absolute; left: 116px; top: 354px; width: 300px;
    text-align: center; font-size: 9.5px; line-height: 11.8px; font-weight: 400;
  }

  .spine-text {
    position: absolute; left: 0; top: 32px; width: 50px; height: 636px;
    writing-mode: vertical-rl; display: flex; align-items: center;
  }
  .spine-title { font-weight: 300; font-size: 17px; }
  .spine-subtitle {
    margin-top: 16px; font-style: italic; font-weight: 300; font-size: 10.5px;
    text-transform: uppercase; color: var(--subtitle-ink);
  }
  .spine-author { margin-top: auto; font-weight: 700; font-size: 9.5px; text-transform: uppercase; }

  .front-cover .stacked-title { right: 262px; top: 248px; }
  .front-cover .subtitle { top: 552px; }
  .front-cover .author { top: 610px; }
</style>
</head>
<body>
  <div class="spread">
    <section class="back-cover">
      <h2 class="stacked-title">The<br>Quiet<br>Harvest<br>of<br>Invention.</h2>
      <div class="title-rule"></div>
      <p class="subtitle">Differences between current period and past</p>
      <p class="author">Dara Tovens</p>
      <p class="blurb">Innovation is not reserved for the gifted or the technical. It grows from a way of seeing that anyone can learn and practise every day. This book sets out a simple frame built on seven key shifts between our time and the past. Each shift opens a field where new ideas take root and ripen with care. Read the shifts well and you will find real openings in work, in trade and in daily life. Steady invention follows from steady attention to how the world has changed. The harvest is quiet, but it is there for those who look closely and act with patience.<br>Innovation is not reserved for the gifted or the technical.</p>
    </section>

    <section class="spine">
      <div class="spine-text">
        <span class="spine-title">The Quiet Harvest of Invention.</span>
        <span class="spine-subtitle">Differences between current period and past</span>
        <span class="spine-author">Dara Tovens</span>
      </div>
    </section>

    <section class="front-cover">
      <div class="front-photo" role="img" aria-label="Photograph of bare light bulbs hanging at different heights on thin black cords against a yellow wall"></div>
      <h1 class="stacked-title">The<br>Quiet<br>Harvest<br>of<br>Invention.</h1>
      <p class="subtitle">Differences between current period and past</p>
      <p class="author">Dara Tovens</p>
    </section>
  </div>
</body>
</html>
```